Drone service provider needs a brilliant web design

I need a responsive web design for a new drone service company. Pelham Drone Solutions provides turnkey solutions to capture, process, and deliver actionable aerial data to customers. The design should communicate a professional company that is safe, legal and insured. I included our logo design and business card designs for reference.
*content to be supplied after design selected

Target Market(s)

We serve telecommunications, construction, government, utility infrastructure, insurance and other industries.

Industry/Entity Type

Industrial

Number of Pages Required

5+ page

Colors

Designer to choose colors to be used in the design.

Requirements
Must have
• The design should highlight professional services to include Inspections, Mapping, Consulting and Training. The site should include aerial images and video to compliment the services offered. The landing page must include following sections in order: HOME, SERVICES, ABOUT, DEMO REEL, CLIENTS, CONTACT FORM, and social media buttons (Facebook, LinkedIn, Twitter, YouTube, Instagram). Contact: 615-382-9041 info@pelhamdronesolutions-example.com Smyrna, TN
• Sitemap:
• 6 pages: Home, Inspections, Mapping, Training, Consulting, About
• HOME (Landing Page)
• • Header with logo and tab links (Home, Services, About, Contact)
• • 'CAPTURE. PROCESS. DELIVER.' tagline and 'CONTACT US' button displayed within aerial image of drone over city or construction site
• • Services section with icons, text and read more link to page
• • About section with photo and text with three icons for SAFE. LEGAL. INSURED.
• • Demo reel
• • Clients logos shown scrolling horizontally
• • Contact form
• • Footer with logo, phone, email, social media buttons
• SERVICES (4 different pages)
• • Inspections
• • Mapping
• • Consulting
• • Training
• ABOUT page
• • Company
• • Partners
• • Certifications & Associations
• • Careers
• CONTACT linked to bottom of landing page
• Would you like to receive the newsletter? Yes or No Drop-down list
Nice to have
• Photos of KVR Marlin or Corvex inspecting infrastructure, buildings, construction sites, etc. A photo of one or two pilots in vest and helmet. Free stock photos preferred but would purchase the right photo that's more relevant.
• website references:
• https://www.quillrotor-example.com/
• https://www.brentfieldworks-example.com/services
• https://www.tomaro-example.com/
• http://gantrymetric-example.com/
• http://lumbrook-example.com/
• http://fennotics-example.com/
• https://www.grebe-example.io/
Should not have
• not an aerial photography or videography service business, no blog or newsletter

```html
<!DOCTYPE html>
<html lang="en">
<head>
<meta charset="utf-8">
<title>Pelham Drone Solutions</title>
<link rel="stylesheet" href="https://fonts.googleapis.com/css2?family=Raleway:wght@400;600;700;800&family=Open+Sans:wght@400;600;700&display=swap">
<style>
:root{
  --blue:#1a8fe3;
  --blue-dark:#0f6fb8;
  --ink:#1c1c1c;
  --text:#555;
  --muted:#8a8a8a;
  --light:#f2f4f6;
  --black:#0b0b0b;
  --white:#fff;
}
*{box-sizing:border-box;margin:0;padding:0}
html,body{width:1200px;height:3012px;overflow:hidden}
body{font-family:"Open Sans",Arial,sans-serif;color:var(--text);background:var(--white);position:relative}

/* top bar */
.topbar{position:absolute;top:0;left:0;width:1200px;height:104px;background:var(--white)}
.social{display:flex;gap:10px}
.social span{width:30px;height:30px;border-radius:50%;background:var(--blue);display:block}
.topbar .social{position:absolute;left:80px;top:36px}
.brand{position:absolute;left:0;width:1200px;top:30px;text-align:center;font-family:"Raleway",sans-serif;font-weight:800;font-size:34px;letter-spacing:1px;color:var(--ink);text-transform:uppercase}
.call{position:absolute;right:80px;top:30px;display:flex;align-items:center;gap:12px}
.call .ic{width:44px;height:44px;border-radius:50%;background:var(--blue);display:flex;align-items:center;justify-content:center}
.call small{display:block;font-size:13px;color:var(--muted)}
.call strong{font-size:22px;color:var(--ink);font-weight:700}

/* nav */
.nav{position:absolute;top:104px;left:0;width:1200px;height:56px;background:var(--blue)}
.nav ul{list-style:none;display:flex;position:absolute;left:260px;top:0;height:56px}
.nav li{padding:0 26px;line-height:56px;color:var(--white);font-size:15px;font-weight:600;text-transform:uppercase;border-right:1px solid rgba(255,255,255,.25)}
.nav li.active{background:#222}
.nav .search{position:absolute;left:908px;top:18px}

/* hero */
.hero{position:absolute;top:160px;left:0;width:1200px;height:400px;background:linear-gradient(180deg,#9fb6c6 0%,#c9d4da 45%,#7d9577 62%,#4d6b45 100%)}
.hero-title{position:absolute;right:90px;top:128px;width:700px;text-align:right;color:var(--white);font-family:"Raleway",sans-serif;font-weight:800;font-size:36px;line-height:46px;text-transform:uppercase;text-shadow:0 2px 6px rgba(0,0,0,.35)}
.badges{position:absolute;right:90px;top:248px;display:flex;gap:22px}
.badge{width:170px;height:56px;border:2px solid var(--white);background:rgba(26,143,227,.35);display:flex;align-items:center;justify-content:center;gap:12px;color:var(--white);font-weight:700;font-size:17px;letter-spacing:1px}
.arrow{position:absolute;width:40px;height:40px;background:rgba(0,0,0,.35);display:flex;align-items:center;justify-content:center}

/* features */
.features{position:absolute;top:560px;left:0;width:1200px;height:270px;background:var(--blue)}
.feature{position:absolute;top:-48px;width:300px;text-align:center;color:var(--white)}
.feature .circle{width:112px;height:112px;border-radius:50%;background:var(--white);border:6px solid var(--blue-dark);margin:0 auto;display:flex;align-items:center;justify-content:center}
.feature h3{font-family:"Raleway",sans-serif;font-weight:800;font-size:22px;margin:20px 0 12px;letter-spacing:1px}
.feature p{font-size:14px;line-height:22px;padding:0 20px}

/* about */
.about h2,.services h2,.contact h2{font-family:"Raleway",sans-serif;font-weight:800;color:var(--ink);text-transform:uppercase}
.about h2{position:absolute;left:80px;top:890px;font-size:46px}
.kicker{font-size:14px;font-weight:700;color:var(--blue);text-transform:uppercase;letter-spacing:1px}
.about .kicker{position:absolute;left:82px;top:950px}
.about .copy{position:absolute;left:80px;top:986px;width:560px;font-size:14px;line-height:24px}
.about .copy p{margin-bottom:12px}
.btn-dark{position:absolute;left:80px;top:1240px;width:150px;height:46px;background:#1d1d1d;color:var(--white);font-weight:700;font-size:14px;text-align:center;line-height:46px;text-transform:uppercase}
.video{position:absolute;left:690px;top:900px;width:430px;height:300px;background:linear-gradient(160deg,#cfd8de 0%,#9fb1bd 50%,#6d7f6a 100%)}
.play{position:absolute;left:185px;top:120px;width:62px;height:62px;border-radius:50%;background:var(--white);display:flex;align-items:center;justify-content:center;box-shadow:0 2px 8px rgba(0,0,0,.3)}

/* services */
.services{position:absolute;top:1380px;left:0;width:1200px;height:610px;background:linear-gradient(180deg,#1f5e8d 0%,#3a87c0 50%,#a9c9df 100%)}
.services h2{position:absolute;top:60px;width:1200px;text-align:center;font-size:42px;color:var(--white)}
.services .kicker{position:absolute;top:118px;width:1200px;text-align:center;color:var(--white)}
.cards{position:absolute;left:72px;top:180px;display:flex;gap:20px}
.card{width:258px}
.card .photo{height:192px}
.card .body{height:190px;background:var(--blue);color:var(--white);text-align:center;padding:22px 20px}
.card h3{font-family:"Raleway",sans-serif;font-weight:800;font-size:22px;margin-bottom:12px;text-transform:uppercase}
.card p{font-size:13px;line-height:21px;margin-bottom:14px}

/* testimonial */
.testimonial{position:absolute;top:2000px;left:0;width:1200px;height:140px;background:var(--black)}
.avatar{position:absolute;left:150px;top:30px;width:80px;height:80px;border-radius:50%;background:linear-gradient(135deg,#6b7a86,#b9c2c9);border:3px solid var(--white)}
.quote{position:absolute;left:260px;top:30px;width:820px;color:#ddd;font-size:14px;line-height:24px;font-style:italic}
.client{position:absolute;right:110px;top:100px;color:var(--blue);font-size:13px;font-weight:700;letter-spacing:1px}
.tarrow{position:absolute;top:52px}

/* contact */
.contact h2{position:absolute;top:2220px;width:1200px;text-align:center;font-size:46px}
.contact .lead{position:absolute;top:2290px;left:220px;width:760px;text-align:center;font-size:14px;line-height:24px}
.contact .note{position:absolute;top:2356px;width:1200px;text-align:center;font-size:16px;color:var(--blue)}
.form{position:absolute;left:236px;top:2408px;width:444px}
.field{height:40px;background:var(--light);border:1px solid #dde1e5;margin-bottom:12px;padding:0 14px;line-height:38px;font-size:13px;color:var(--muted)}
.field.area{height:90px}
.submit{height:46px;background:var(--blue);color:var(--white);font-weight:700;font-size:16px;text-align:center;line-height:46px;text-transform:uppercase;margin-top:12px}
.info{position:absolute;left:720px;top:2408px;width:320px}
.info h4{font-family:"Raleway",sans-serif;font-weight:800;font-size:17px;color:var(--ink);text-transform:uppercase;margin-bottom:14px}
.info .name{font-size:13px;font-weight:700;color:var(--ink);margin-bottom:16px;text-transform:uppercase}
.info .row{display:flex;align-items:center;gap:12px;font-size:13px;margin-bottom:14px;white-space:nowrap}
.info .dot{width:26px;height:26px;border-radius:50%;background:#333;display:flex;align-items:center;justify-content:center;flex:none}
.info .follow{margin-top:26px}

/* footer */
.footer{position:absolute;top:2760px;left:0;width:1200px;height:252px;background:var(--black);text-align:center}
.footer .brand{top:60px;color:var(--white)}
.footer .links{position:absolute;top:140px;width:1200px;display:flex;justify-content:center;gap:24px;color:#ccc;font-size:14px}
.footer .copy{position:absolute;top:176px;width:1200px;font-size:13px;color:#888}
</style>
</head>
<body>

<header class="topbar">
  <div class="social"><span></span><span></span><span></span><span></span></div>
  <div class="brand">Pelham Drone Solutions</div>
  <div class="call">
    <div class="ic"><svg width="20" height="20" viewBox="0 0 24 24"><path fill="#fff" d="M6.6 10.8a15 15 0 0 0 6.6 6.6l2.2-2.2c.3-.3.7-.4 1-.2 1.1.4 2.3.6 3.6.6.6 0 1 .4 1 1V20c0 .6-.4 1-1 1A17 17 0 0 1 3 4c0-.6.4-1 1-1h3.5c.6 0 1 .4 1 1 0 1.3.2 2.5.6 3.6.1.3 0 .7-.2 1z"/></svg></div>
    <div><small>Call Us Today!</small><strong>615-382-9041</strong></div>
  </div>
</header>

<nav class="nav">
  <ul><li class="active">Home</li><li>About Us</li><li>Services</li><li>Contact Us</li></ul>
  <svg class="search" width="20" height="20" viewBox="0 0 24 24"><circle cx="10" cy="10" r="6.5" fill="none" stroke="#fff" stroke-width="2.5"/><path d="M15 15l6 6" stroke="#fff" stroke-width="2.5"/></svg>
</nav>

<section class="hero" role="img" aria-label="Drone pilot at a field flying a quadcopter over open land">
  <div class="hero-title">On Demand Customized Drone<br>Solutions Pelham For You</div>
  <div class="badges">
    <div class="badge"><svg width="22" height="22" viewBox="0 0 24 24"><path d="M12 2l8 3v6c0 5-3.5 9-8 11-4.5-2-8-6-8-11V5z" fill="none" stroke="#fff" stroke-width="2"/><path d="M8 12l3 3 5-6" fill="none" stroke="#fff" stroke-width="2"/></svg>SAFE</div>
    <div class="badge"><svg width="22" height="22" viewBox="0 0 24 24"><rect x="4" y="3" width="16" height="18" fill="none" stroke="#fff" stroke-width="2"/><path d="M8 12l3 3 5-6" fill="none" stroke="#fff" stroke-width="2"/></svg>LEGAL</div>
    <div class="badge"><svg width="22" height="22" viewBox="0 0 24 24"><circle cx="12" cy="12" r="9" fill="none" stroke="#fff" stroke-width="2"/><path d="M8 12l3 3 5-6" fill="none" stroke="#fff" stroke-width="2"/></svg>INSURED</div>
  </div>
</section>
<div class="arrow" style="left:0;top:380px"><svg width="14" height="14" viewBox="0 0 14 14"><path d="M9 2L4 7l5 5" fill="none" stroke="#fff" stroke-width="2"/></svg></div>
<div class="arrow" style="right:0;top:380px"><svg width="14" height="14" viewBox="0 0 14 14"><path d="M5 2l5 5-5 5" fill="none" stroke="#fff" stroke-width="2"/></svg></div>

<section class="features">
  <div class="feature" style="left:150px">
    <div class="circle"><svg width="52" height="52" viewBox="0 0 48 48"><rect x="6" y="14" width="36" height="24" rx="3" fill="var(--blue)"/><rect x="17" y="9" width="14" height="7" fill="var(--blue)"/><circle cx="24" cy="26" r="7" fill="#fff"/><circle cx="24" cy="26" r="4" fill="var(--blue)"/></svg></div>
    <h3>CAPTURE</h3>
    <p>Lorem Ipsum is simply dummy text of the printing and typesetting industry. Lorem Ipsum has been the industry's.</p>
  </div>
  <div class="feature" style="left:450px">
    <div class="circle"><svg width="54" height="54" viewBox="0 0 48 48"><g fill="var(--blue)"><circle cx="24" cy="24" r="13"/><rect x="21" y="4" width="6" height="40"/><rect x="4" y="21" width="40" height="6"/><rect x="21" y="4" width="6" height="40" transform="rotate(45 24 24)"/><rect x="21" y="4" width="6" height="40" transform="rotate(-45 24 24)"/></g><circle cx="24" cy="24" r="6" fill="#fff"/></svg></div>
    <h3>PROCESS</h3>
    <p>Lorem Ipsum is simply dummy text of the printing and typesetting industry. Lorem Ipsum has been the industry's.</p>
  </div>
  <div class="feature" style="left:750px">
    <div class="circle"><svg width="50" height="50" viewBox="0 0 48 48"><path d="M10 4h20l8 8v32H10z" fill="var(--blue)"/><path d="M18 26h14M26 20l6 6-6 6" fill="none" stroke="#fff" stroke-width="3"/></svg></div>
    <h3>DELIVER DATA</h3>
    <p>Lorem Ipsum is simply dummy text of the printing and typesetting industry. Lorem Ipsum has been the industry's.</p>
  </div>
</section>

<section class="about">
  <h2>About Us</h2>
  <div class="kicker">Who We Are</div>
  <div class="copy">
    <p>Lorem Ipsum is simply dummy text of the printing and typesetting industry. Lorem Ipsum has been the industry's standard dummy text ever since.</p>
    <p>Lorem Ipsum is simply dummy text of the printing and typesetting industry. Lorem Ipsum has been the industry's standard dummy text ever since the 1500s, when an unknown printer took a galley of type and scrambled it to make a type. Lorem Ipsum is simply dummy text of the printing and typesetting industry.</p>
  </div>
  <div class="btn-dark">Learn More</div>
  <div class="video" role="img" aria-label="Demo reel video still of a drone ready for flight in a hangar">
    <div class="play"><svg width="24" height="24" viewBox="0 0 24 24"><path d="M7 4l14 8-14 8z" fill="var(--blue)"/></svg></div>
  </div>
</section>

<section class="services">
  <h2>Services We Provide You</h2>
  <div class="kicker">Drone Solutions</div>
  <div class="cards">
    <div class="card">
      <div class="photo" role="img" aria-label="Inspector reviewing a checklist on a clipboard" style="background:linear-gradient(135deg,#d9dde0,#8c98a2)"></div>
      <div class="body"><h3>Inspections</h3><p>Lorem Ipsum is simply dummy text of the printing and typesetting industry. Lorem Ipsum.</p><svg width="30" height="12" viewBox="0 0 30 12"><path d="M0 6h26M21 1l6 5-6 5" fill="none" stroke="#fff" stroke-width="2"/></svg></div>
    </div>
    <div class="card">
      <div class="photo" role="img" aria-label="Drone hovering over a survey site for mapping" style="background:linear-gradient(135deg,#c6cfd6,#5f6d78)"></div>
      <div class="body"><h3>Mapping</h3><p>Lorem Ipsum is simply dummy text of the printing and typesetting industry. Lorem Ipsum.</p><svg width="30" height="12" viewBox="0 0 30 12"><path d="M0 6h26M21 1l6 5-6 5" fill="none" stroke="#fff" stroke-width="2"/></svg></div>
    </div>
    <div class="card">
      <div class="photo" role="img" aria-label="Consultant in a business meeting" style="background:linear-gradient(135deg,#aab7c3,#2f4658)"></div>
      <div class="body"><h3>Consulting</h3><p>Lorem Ipsum is simply dummy text of the printing and typesetting industry. Lorem Ipsum.</p><svg width="30" height="12" viewBox="0 0 30 12"><path d="M0 6h26M21 1l6 5-6 5" fill="none" stroke="#fff" stroke-width="2"/></svg></div>
    </div>
    <div class="card">
      <div class="photo" role="img" aria-label="Training session in a classroom" style="background:linear-gradient(135deg,#d8d3c8,#7e8a86)"></div>
      <div class="body"><h3>Training</h3><p>Lorem Ipsum is simply dummy text of the printing and typesetting industry. Lorem Ipsum.</p><svg width="30" height="12" viewBox="0 0 30 12"><path d="M0 6h26M21 1l6 5-6 5" fill="none" stroke="#fff" stroke-width="2"/></svg></div>
    </div>
  </div>
</section>

<section class="testimonial">
  <svg class="tarrow" style="left:40px" width="20" height="36" viewBox="0 0 20 36"><path d="M16 2L4 18l12 16" fill="none" stroke="#fff" stroke-width="2.5"/></svg>
  <div class="avatar" role="img" aria-label="Client portrait"></div>
  <p class="quote">" Lorem Ipsum is simply dummy text of the printing and typesetting industry. Lorem Ipsum has been the industry's standard dummy text ever since the 1500s, when an unknown printer took a galley of type and scrambled it to make a type. "</p>
  <div class="client">— CLIENTNAME</div>
  <svg class="tarrow" style="right:40px" width="20" height="36" viewBox="0 0 20 36"><path d="M4 2l12 16L4 34" fill="none" stroke="#fff" stroke-width="2.5"/></svg>
</section>

<section class="contact">
  <h2>Contact Us</h2>
  <p class="lead">Lorem Ipsum is simply dummy text of the printing and typesetting industry. Lorem Ipsum has been the industry's standard dummy text ever since the 1500s, when an unknown printer.</p>
  <p class="note">Fill out the below and one of our Representative will Contact you shortly</p>
  <div class="form">
    <div class="field">Name *</div>
    <div class="field">Email *</div>
    <div class="field">Phone *</div>
    <div class="field area">Message *</div>
    <div class="submit">Submit</div>
  </div>
  <div class="info">
    <h4>Contact Us</h4>
    <div class="name">Pelham Drone Solution</div>
    <div class="row"><span class="dot"><svg width="12" height="12" viewBox="0 0 24 24"><path fill="#fff" d="M6.6 10.8a15 15 0 0 0 6.6 6.6l2.2-2.2c.3-.3.7-.4 1-.2 1.1.4 2.3.6 3.6.6.6 0 1 .4 1 1V20c0 .6-.4 1-1 1A17 17 0 0 1 3 4c0-.6.4-1 1-1h3.5c.6 0 1 .4 1 1 0 1.3.2 2.5.6 3.6.1.3 0 .7-.2 1z"/></svg></span>615-382-9041</div>
    <div class="row"><span class="dot"><svg width="12" height="12" viewBox="0 0 24 24"><rect x="2" y="5" width="20" height="14" fill="#fff"/><path d="M2 5l10 8 10-8" fill="none" stroke="#333" stroke-width="2"/></svg></span>info@pelhamdronesolutions-example.com</div>
    <div class="row"><span class="dot"><svg width="12" height="12" viewBox="0 0 24 24"><circle cx="12" cy="12" r="9" fill="none" stroke="#fff" stroke-width="2"/><path d="M3 12h18M12 3c4 4 4 14 0 18M12 3c-4 4-4 14 0 18" fill="none" stroke="#fff" stroke-width="1.5"/></svg></span>www.pelhamdronesolutions-example.com</div>
    <h4 class="follow">Follow Us</h4>
    <div class="social"><span></span><span></span><span></span><span></span></div>
  </div>
</section>

<footer class="footer">
  <div class="brand">Pelham Drone Solutions</div>
  <div class="links"><span>Home</span><span>About</span><span>Services</span><span>Contact</span></div>
  <div class="copy">© PELHAM DRONE SOLUTION - All Rights Reserved.</div>
</footer>

</body>
</html>
```